Stationery Design Project

I need a stationary design for our company. we are based in Houston, TX and we are called Mira Vell Lending. And we are wanting to brand our MoneyMendPlus program, which includes our tax preparation and restoration, credit repair service. Although our business offers other programs, we are interested in mainly focusing on The MoneyMendPlus program. We are looking for way to brand our ourselves and I believe that a great stationery design will help in achieving this goal. Our logo design is blue and light blue. the slogan is orange.

Industry/Entity Type

Business

Requirements
Must have
• Address: 30871 Calloway Ln. B-22
Houston, TX 75419
Tel. 555-318-6207
Fax 555-294-7153
www.miravelllending.example
info@miravelllending.example
Our Slogan: Confidence, Renewed!

```html
<!DOCTYPE html>
<html lang="en">
<head>
<meta charset="utf-8">
<title>MoneyMendPlus Business Cards</title>
<link rel="stylesheet" href="https://fonts.googleapis.com/css2?family=Jost:wght@400;500&family=Tinos:wght@400&display=swap">
<style>
  :root {
    --navy: #173e6b;
    --blue: #1a5e98;
    --sky: #1b8fcc;
    --orange: #f39a1e;
    --white: #ffffff;
    --paper: #eef1f4;
    --ink-soft: rgba(255,255,255,0.14);
  }
  * { box-sizing: border-box; margin: 0; padding: 0; }
  html, body { width: 1200px; height: 723px; overflow: hidden; }
  body {
    background: var(--paper);
    font-family: "Jost", Arial, sans-serif;
    position: relative;
  }
  .card {
    position: absolute;
    top: 206px;
    width: 540px;
    height: 310px;
    border-radius: 22px;
    overflow: hidden;
    box-shadow: 0 6px 18px rgba(0,0,0,0.18);
  }
  /* Front */
  .card-front { left: 45px; background: var(--white); }
  .card-front .waves { position: absolute; inset: 0; width: 100%; height: 100%; }
  .brand-name {
    position: absolute;
    left: 70px; top: 76px;
    font-family: "Tinos", "Times New Roman", serif;
    font-size: 46px;
    line-height: 1.1;
    color: var(--blue);
    letter-spacing: -0.5px;
  }
  .slogan {
    position: absolute;
    left: 100px; top: 134px;
    font-family: "Tinos", "Times New Roman", serif;
    font-size: 21px;
    line-height: 1.1;
    color: var(--orange);
    letter-spacing: 2.5px;
  }
  .partner-mark {
    position: absolute;
    right: 36px; top: 24px;
    width: 96px; height: 96px;
    background: var(--navy);
    border: 3px solid #c9d6e6;
    display: flex; align-items: center; justify-content: center;
    text-align: center;
    font-family: "Tinos", "Times New Roman", serif;
    font-size: 13px;
    line-height: 1.2;
    color: var(--white);
    padding: 6px;
  }
  .address {
    position: absolute;
    left: 96px; top: 242px;
    width: 180px;
    text-align: right;
    color: var(--white);
    font-size: 14.5px;
    line-height: 19px;
  }
  .divider {
    position: absolute;
    left: 290px; top: 232px;
    width: 1px; height: 68px;
    background: rgba(255,255,255,0.8);
  }
  .contact-list {
    position: absolute;
    left: 302px; top: 230px;
    list-style: none;
    color: var(--white);
    font-size: 13.5px;
    line-height: 18.5px;
  }
  .contact-list li { display: flex; align-items: center; gap: 6px; }
  .contact-list svg { width: 11px; height: 11px; flex: none; }
  /* Back */
  .card-back {
    left: 615px;
    background: radial-gradient(ellipse at 50% 50%, #1f79b8 0%, #17578f 50%, #133f70 100%);
  }
  .back-frame {
    position: absolute;
    left: 110px; top: 28px;
    width: 300px; height: 250px;
    border: 2px solid var(--ink-soft);
    background: rgba(255,255,255,0.04);
  }
  .back-rule {
    position: absolute;
    left: 70px; top: 116px;
    width: 360px; height: 2px;
    background: var(--white);
  }
  .back-name {
    position: absolute;
    left: 0; right: 0; top: 122px;
    text-align: center;
    font-family: "Tinos", "Times New Roman", serif;
    font-size: 56px;
    line-height: 64px;
    color: var(--white);
  }
  .back-rule-under {
    position: absolute;
    left: 110px; top: 190px;
    width: 340px; height: 2px;
    background: var(--white);
  }
  .back-faint-name {
    position: absolute;
    left: 0; right: 0; top: 198px;
    text-align: center;
    font-family: "Tinos", "Times New Roman", serif;
    font-size: 24px;
    line-height: 30px;
    color: var(--ink-soft);
  }
  .back-web {
    position: absolute;
    left: 0; right: 0; top: 238px;
    text-align: center;
    font-family: "Tinos", "Times New Roman", serif;
    font-size: 14px;
    line-height: 18px;
    letter-spacing: 3.5px;
    color: var(--white);
  }
</style>
</head>
<body>
  <section class="card card-front">
    <svg class="waves" viewBox="0 0 540 310" preserveAspectRatio="none" aria-hidden="true">
      <defs>
        <linearGradient id="band-fill" x1="0" y1="0" x2="1" y2="0">
          <stop offset="0" stop-color="#1a4f86"/>
          <stop offset="0.55" stop-color="#1a6aa8"/>
          <stop offset="1" stop-color="#1b8fcc"/>
        </linearGradient>
      </defs>
      <path d="M0 215 C 170 245, 360 225, 540 115 L540 310 L0 310 Z" fill="url(#band-fill)"/>
      <path d="M0 195 C 170 225, 360 210, 480 140 C 370 215, 170 238, 0 208 Z" fill="var(--orange)"/>
    </svg>
    <div class="brand-name">MoneyMendPlus</div>
    <div class="slogan">Confidence, Renewed!</div>
    <div class="partner-mark">Mira Vell Lending</div>
    <div class="address">30871 Calloway Ln. B-22<br>Houston<br>TX 75419</div>
    <div class="divider"></div>
    <ul class="contact-list">
      <li><svg viewBox="0 0 12 12"><path d="M2 1 L4.5 1 L5.5 3.5 L4 4.5 C4.8 6.2 5.8 7.2 7.5 8 L8.5 6.5 L11 7.5 L11 10 C6 10.5 1.5 6 2 1 Z" fill="#fff"/></svg>555-318-6207</li>
      <li><svg viewBox="0 0 12 12"><rect x="1" y="4" width="10" height="6" rx="1" fill="#fff"/><rect x="3" y="1" width="6" height="3" fill="#fff"/></svg>555-294-7153</li>
      <li><svg viewBox="0 0 12 12"><rect x="1" y="2.5" width="10" height="7" rx="1" fill="#fff"/><path d="M1.5 3 L6 6.5 L10.5 3" stroke="#1a5e98" fill="none"/></svg>info@miravelllending.example</li>
      <li><svg viewBox="0 0 12 12"><circle cx="6" cy="6" r="5" fill="none" stroke="#fff"/><ellipse cx="6" cy="6" rx="2.2" ry="5" fill="none" stroke="#fff"/><line x1="1" y1="6" x2="11" y2="6" stroke="#fff"/></svg>www.miravelllending.example</li>
    </ul>
  </section>

  <section class="card card-back">
    <div class="back-frame"></div>
    <div class="back-rule"></div>
    <div class="back-name">MoneyMendPlus</div>
    <div class="back-rule-under"></div>
    <div class="back-faint-name">Mira Vell Lending</div>
    <div class="back-web">www.miravelllending.example</div>
  </section>
</body>
</html>
```